Local Flower Farm Needs Business Card Design

I need business cards designed for a flower farm based in Eudora, Kansas.
Business Info:
We are a local cut flower farm located in Eudora, Kansas, founded by Corinne Haldwick. What started as a passion for agriculture and search for more joy in daily life has blossomed into a small business dedicated to providing the community with beautiful, fresh, and sustainable flowers. We specialize in local, seasonal blooms, ensuring that every petal reflects the care and dedication we pour into our craft. Our mission is to deliver the highest quality flowers directly to our customers through local farmers markets and to florists who share our commitment to sustainability. Join us in celebrating the beauty of nature, one bloom at a time!
Contact Details:
Corinne Haldwick
Owner
Phone 913-555-0147
Facebook: Rosalind Thorpe Gardens
Instagram: @RosalindThorpeGardens
Website: RosalindThorpeGardens.example
Target Market(s)
Wholesale to Florists and Direct to Consumer via Farmers Market
Industry/Entity Type
Florist, Farm
Contact Information for Business Card
Name, Contact Info, Logo
Look and feel
Each slider illustrates characteristics of the customer's brand and the style your logo design should communicate.

```html
<!DOCTYPE html>
<html lang="en">
<head>
<meta charset="utf-8">
<title>Rosalind Thorpe Gardens – Business Card</title>
<link rel="stylesheet" href="https://fonts.googleapis.com/css2?family=Tinos:wght@400;700&display=swap">
<style>
  :root {
    --backdrop: #e0e4e7;
    --forest: #0b2730;
    --paper: #ffffff;
    --ink: #111111;
    --fold-shade: #a9a9a9;
  }
  * { margin: 0; padding: 0; box-sizing: border-box; }
  html, body {
    width: 1200px; height: 960px; overflow: hidden;
    background: var(--backdrop);
    font-family: "Tinos", "Times New Roman", serif;
  }
  .card {
    position: absolute;
    box-shadow: 0 10px 22px rgba(0,0,0,.28);
  }
  .card-front {
    left: 246px; top: 58px; width: 709px; height: 405px;
    background: var(--forest);
  }
  .card-back {
    left: 249px; top: 500px; width: 702px; height: 400px;
    background: var(--paper);
    overflow: hidden;
  }
  .brand-seal {
    position: absolute;
    border-radius: 50%;
    display: flex; align-items: center; justify-content: center;
    text-align: center;
  }
  .card-front .brand-seal {
    left: 219px; top: 67px; width: 270px; height: 270px;
    border: 1px solid var(--paper);
  }
  .card-back .brand-seal {
    left: 26px; top: 26px; width: 200px; height: 200px;
    border: 1px solid var(--forest);
  }
  .brand-name {
    font-weight: 400;
    letter-spacing: 2px;
    text-transform: uppercase;
    line-height: 1.35;
  }
  .card-front .brand-name { color: var(--paper); font-size: 24px; }
  .card-back .brand-name { color: var(--forest); font-size: 18px; }
  .fold-shade {
    position: absolute; left: 0; top: 0;
    width: 702px; height: 400px;
  }
  .holder {
    position: absolute; right: 27px; top: 170px;
    text-align: right; color: var(--ink);
  }
  .holder-name { font-weight: 700; font-size: 35px; letter-spacing: .5px; line-height: 1; }
  .holder-role { font-size: 16px; margin-top: 2px; letter-spacing: .5px; }
  .accent-bar {
    position: absolute; left: 685px; top: 186px;
    width: 17px; height: 44px; background: var(--ink);
  }
  .contact-list {
    position: absolute; right: 60px; top: 282px;
    list-style: none; text-align: right;
    font-size: 17px; color: var(--ink); letter-spacing: .3px;
  }
  .contact-list li { height: 24px; line-height: 24px; }
  .contact-icons {
    position: absolute; left: 658px; top: 284px;
    width: 18px; height: 96px;
  }
</style>
</head>
<body>

<section class="card card-front">
  <div class="brand-seal">
    <span class="brand-name">Rosalind<br>Thorpe<br>Gardens</span>
  </div>
</section>

<section class="card card-back">
  <svg class="fold-shade" viewBox="0 0 702 400" aria-hidden="true">
    <defs>
      <linearGradient id="shade" x1="0" y1="1" x2="0.2" y2="0">
        <stop offset="0" stop-color="var(--fold-shade)" stop-opacity=".75"/>
        <stop offset="1" stop-color="var(--paper)" stop-opacity="0"/>
      </linearGradient>
    </defs>
    <polygon points="676,24 676,40 26,372 28,370" fill="url(#shade)"/>
    <polygon points="670,26 24,372 40,380 676,38" fill="var(--fold-shade)" opacity=".35"/>
  </svg>

  <div class="brand-seal">
    <span class="brand-name">Rosalind<br>Thorpe<br>Gardens</span>
  </div>

  <div class="holder">
    <p class="holder-name">Corinne Haldwick</p>
    <p class="holder-role">Owner</p>
  </div>
  <div class="accent-bar"></div>

  <ul class="contact-list">
    <li>913-555-0147</li>
    <li>Rosalind Thorpe Gardens</li>
    <li>@RosalindThorpeGardens</li>
    <li>RosalindThorpeGardens.example</li>
  </ul>

  <svg class="contact-icons" viewBox="0 0 18 96" aria-hidden="true">
    <path d="M4 3 C2 5 2 8 5 12 C8 16 11 17 13 15 L14 13 L11 11 L10 12 C8 11 7 10 6 8 L7 7 L5 4 Z" fill="var(--forest)"/>
    <path d="M11 3 A4 4 0 0 1 15 7 M11 5.5 A1.8 1.8 0 0 1 13 7.5" stroke="var(--forest)" fill="none" stroke-width="1.2"/>
    <circle cx="9" cy="33" r="8" fill="var(--forest)"/>
    <rect x="1.5" y="50" width="15" height="15" rx="4" fill="none" stroke="var(--forest)" stroke-width="2"/>
    <circle cx="9" cy="81" r="7.5" fill="var(--forest)"/>
    <path d="M1.5 81 H16.5 M9 73.5 C5 77 5 85 9 88.5 C13 85 13 77 9 73.5" stroke="var(--paper)" stroke-width="1" fill="none"/>
  </svg>
</section>

</body>
</html>
```